Harbor Loom Floors Letterhead

Letterhead used for business reasons. It must be editable and easy to use.

Address is 2715 W. Pelican Lane Englewood FL 34187 - 941.382.6519

```html
<!DOCTYPE html>
<html lang="en">
<head>
<meta charset="utf-8">
<title>Harbor Loom Floors Letterhead</title>
<link rel="stylesheet" href="https://fonts.googleapis.com/css2?family=Lato:wght@400;700&family=Montserrat:wght@400&display=swap">
<style>
  :root {
    --canvas: #e9e7e4;
    --paper: #ffffff;
    --header: #181818;
    --accent: #e08b25;
    --ink: #1a1a1a;
    --muted: #bdb9b6;
    --curve-grey: #9b9693;
  }
  html, body {
    margin: 0;
    width: 1200px;
    height: 1200px;
    overflow: hidden;
    background: var(--canvas);
  }
  .letterhead {
    position: absolute;
    left: 210px;
    top: 50px;
    width: 780px;
    height: 1100px;
    background: var(--paper);
    box-shadow: 0 6px 24px rgba(0,0,0,0.15);
    overflow: hidden;
    font-family: "Lato", sans-serif;
    color: var(--ink);
  }
  .header-band {
    position: absolute;
    left: 0; top: 0;
    width: 100%;
    height: 185px;
    background: var(--header);
  }
  .brand-name {
    position: absolute;
    left: 48px;
    top: 74px;
    margin: 0;
    font-family: "Lato", sans-serif;
    font-weight: 400;
    font-size: 30px;
    letter-spacing: 1px;
    color: var(--accent);
  }
  .contact-block {
    position: absolute;
    right: 44px;
    top: 58px;
    display: flex;
    align-items: stretch;
    gap: 22px;
  }
  .contact-divider {
    width: 2px;
    background: var(--accent);
  }
  .contact-lines {
    font-family: "Montserrat", sans-serif;
    font-size: 12.5px;
    line-height: 1.55;
    color: #ffffff;
  }
  .contact-phone {
    display: flex;
    align-items: center;
    gap: 6px;
    margin-top: 6px;
  }
  .letter-body {
    position: absolute;
    left: 62px;
    right: 56px;
    top: 236px;
    font-size: 14.5px;
    line-height: 1.3;
  }
  .letter-date { margin: 0 0 18px; }
  .recipient { margin: 0 0 22px 10px; }
  .recipient-company { margin: 0 0 26px 20px; }
  .salutation {
    margin: 0 0 26px 30px;
    font-weight: 700;
    font-size: 19px;
  }
  .paragraph { margin: 0 0 20px 40px; }
  .closing { margin: 34px 0 0 50px; }
  .signature {
    margin: 26px 0 0 70px;
    width: 230px;
    height: 56px;
    background: linear-gradient(90deg, #ececec, #f6f6f6);
    border-radius: 4px;
  }
  .footer-wave {
    position: absolute;
    left: 0;
    bottom: 0;
    width: 780px;
    height: 260px;
  }
</style>
</head>
<body>
  <main class="letterhead">
    <header class="header-band">
      <h1 class="brand-name">Harbor Loom Floors</h1>
      <div class="contact-block">
        <span class="contact-divider"></span>
        <div class="contact-lines">
          <div>2715 W. Pelican Lane</div>
          <div>Englewood FL 34187</div>
          <div class="contact-phone">
            <svg width="11" height="11" viewBox="0 0 24 24" aria-hidden="true">
              <path fill="#e08b25" d="M6.6 10.8a15.1 15.1 0 0 0 6.6 6.6l2.2-2.2a1 1 0 0 1 1-.25 11.4 11.4 0 0 0 3.6.57 1 1 0 0 1 1 1V20a1 1 0 0 1-1 1A17 17 0 0 1 3 4a1 1 0 0 1 1-1h3.5a1 1 0 0 1 1 1 11.4 11.4 0 0 0 .57 3.6 1 1 0 0 1-.25 1z"/>
            </svg>
            <span>941.382.6519</span>
          </div>
        </div>
      </div>
    </header>

    <section class="letter-body">
      <p class="letter-date">January-03-2020</p>
      <p class="recipient">Mr, Owen Hale<br>President</p>
      <p class="recipient-company">Crestline Corporation<br>123 Street Name, Suite# 10<br>City, State, 120023</p>
      <p class="salutation">Dear Mr, Owen</p>
      <p class="paragraph">Lorem ipsum dolor sit amet, consectetur adipiscing elit, sed do eiusmod tempor incididunt ut labore et dolore magna aliqua. Ut enim ad minim veniam, quis nostrud exercitation ullamco laboris nisi ut aliquip ex ea commodo consequat. Duis aute irure dolor in reprehenderit in voluptate velit esse cillum dolore eu fugiat nulla pariatur.</p>
      <p class="paragraph">Lorem ipsum dolor sit amet, consectetur adipiscing elit, sed do eiusmod tempor incididunt ut labore et dolore magna aliqua. Ut enim ad minim veniam, quis nostrud exercitation ullamco laboris nisi ut aliquip ex ea commodo consequat. Duis aute irure dolor in reprehenderit in voluptate velit esse cillum dolore eu fugiat nulla pariatur.</p>
      <p class="paragraph">Lorem ipsum dolor sit amet, consectetur adipiscing elit, sed do eiusmod tempor incididunt ut labore et dolore magna aliqua. Ut enim ad minim veniam, quis nostrud exercitation ullamco laboris nisi ut aliquip ex ea commodo consequat.</p>
      <p class="paragraph">Excepteur sint occaecat cupidatat non proident, sunt in culpa qui officia deserunt mollit anim id est laborum. re et dolore magnam aliquam quaerat voluptatem.</p>
      <p class="closing">Regards</p>
      <div class="signature" role="img" aria-label="Handwritten signature of Nadia Brooks"></div>
    </section>

    <svg class="footer-wave" viewBox="0 0 780 260" preserveAspectRatio="none" aria-hidden="true">
      <path d="M0 260 L0 236 C 190 150, 470 150, 780 0 L780 260 Z" fill="var(--accent)"/>
      <path d="M0 236 C 170 120, 480 120, 760 18" fill="none" stroke="var(--curve-grey)" stroke-width="4"/>
      <path d="M0 238 C 180 135, 480 135, 770 14" fill="none" stroke="var(--muted)" stroke-width="2"/>
    </svg>
  </main>
</body>
</html>
```